Custom PowerPoint Template for Training & Workshop Presentations

I am looking for a professional designer to create a custom PowerPoint template (PPTX) for my training and workshop materials. My trainings are designed for: HR professionals and Learning & Development specialists;
Executives and team leaders; Organizations investing in employee development and workplace learning; Participants in professional development workshops, seminars, and didactics trainings
The template should therefore appear trustworthy, calm, friendly, structured, and competence‑oriented. The design should be visually appealing, easy to read, and fully editable.

All branding files are attached to this project.
Please use them as the main reference for your design:
Logo (included as attachment)
Brand color specifications (included as attachment)
Font specifications related to the logo and brand (included as attachment)

What I need:
--> Title Slide: Title, subtitle, name, logo
(1–2 variations)
--> Agenda / Overview Slide
--> Content Slides
--> Text only
--> Text + image
-->Two-column
--> Section header
--> Quote / key message
--> Graphic / Model Slides: (1–2 layouts for frameworks, processes, models)
--> Tables & Charts: (Table styles in brand colors; Chart design aligned with typography and color palette)
--> Closing Slide: (Contact or call-to-action; Optional second variation)

All layouts must be built properly inside the PowerPoint Slide Master

```html
<!DOCTYPE html>
<html lang="de">
<head>
<meta charset="utf-8">
<title>Präsentationsvorlage – Schulungen &amp; Workshops</title>
<link href="https://fonts.googleapis.com/css2?family=Open+Sans:wght@400;600;700;800&family=Roboto+Condensed:wght@500;700&display=swap" rel="stylesheet">
<style>
:root{
  --blue:#1f5c99;
  --blue-deep:#174a7e;
  --mist:#8aa6c2;
  --mist-light:#b9cadb;
  --pale:#e8eef5;
  --ink:#1d1d1d;
  --text:#4b4b4b;
  --rule:#cfd8e2;
  --canvas:#d5d6d2;
}
*{box-sizing:border-box;margin:0;padding:0}
html,body{width:1200px;height:1200px;overflow:hidden;background:var(--canvas)}
.board{display:grid;grid-template-columns:repeat(4,281px);grid-template-rows:repeat(7,157px);gap:7.6px 6.5px;padding:27px 0 0 27px}
.cell{position:relative;overflow:hidden;background:#fff;box-shadow:0 1px 3px rgba(0,0,0,.18)}
.slide{position:absolute;left:0;top:0;width:453px;height:253px;transform:scale(.6203);transform-origin:0 0;font-family:'Open Sans',sans-serif;color:var(--ink)}
.slide > *{position:absolute}
.pg{top:9px;right:10px;font-size:6px;border-bottom:.6px solid #333;line-height:1.3}
.foot{right:10px;bottom:6px;display:flex;align-items:center;gap:2px;font-family:'Roboto Condensed',sans-serif;font-weight:700;font-size:5px;color:var(--blue)}
.foot i{display:block;width:6px;height:6px;border:.8px solid var(--blue)}
.h1{font-weight:700;font-size:19px;color:var(--ink);white-space:nowrap}
.lead{font-size:15px;line-height:1.15;white-space:nowrap}
.lead b{font-weight:600}
.copy{font-size:5.6px;line-height:1.6;color:var(--text)}
.copy.j{text-align:justify}
.bar{width:12px;height:4px;background:var(--mist)}
.ph{background:linear-gradient(135deg,#9fb1c4,#5d7288 60%,#3b4c5e)}
.ph.warm{background:linear-gradient(135deg,#c9a98c,#7f6a5a 55%,#3e3a3b)}
.ph.sky{background:linear-gradient(170deg,#e7edf3,#a8bdd1 55%,#4d6278)}
.ph.room{background:linear-gradient(160deg,#dcd9d3,#a99f93 50%,#5a5550)}
.dot{border-radius:50%;background:var(--blue);display:flex;align-items:center;justify-content:center}
.cap{font-weight:700;font-size:6px;text-transform:uppercase;letter-spacing:.2px}
.svc-head{font-size:15px;font-weight:700;line-height:1.05;white-space:nowrap}
.c{text-align:center}
.r{text-align:right}
</style>
</head>
<body>
<main class="board">

<!-- 1 title -->
<section class="cell"><div class="slide">
  <div style="left:0;right:0;top:66px;display:flex;justify-content:center;align-items:center;gap:5px;font-family:'Roboto Condensed',sans-serif;font-weight:700;font-size:15px;color:var(--blue)"><i style="display:block;width:14px;height:14px;border:1.4px solid var(--blue)"></i>Dr. Lena Hartwig-Brandt</div>
  <div class="c" style="left:0;right:0;top:118px;font-size:20px;font-weight:600;line-height:1.25;color:#2b2b2b">Schulungen &amp; Workshops<br>Präsentationen</div>
  <div class="c copy" style="left:0;right:0;top:190px;color:#333">www.lenahartwig.de</div>
</div></section>

<!-- 2 contact -->
<section class="cell"><div class="slide">
  <div class="pg">2</div>
  <div class="c" style="left:0;right:0;top:54px;font-size:17px;font-weight:600">Kontakte</div>
  <div class="c copy" style="left:0;right:0;top:88px;color:#333">Dr. phil. Lena Hartwig-Brandt, MBA<br>Lindenweg 12<br>96047 BAMBERG<br><br><b>TELEFON</b><br>01520 / 480 16 93<br><br><b>EMAIL</b><br>info@lenahartwig.de</div>
</div></section>

<!-- 3 agenda -->
<section class="cell"><div class="slide">
  <div class="pg">3</div>
  <div class="c" style="left:0;right:0;top:18px;font-size:17px;font-weight:600">Inhalt</div>
  <div style="left:176px;top:52px;display:grid;grid-template-columns:20px auto;row-gap:5.5px;align-items:center">
    <span style="font-size:11px;color:var(--mist)">1</span><span class="cap" style="font-size:5px">Zusammenfassung</span>
    <span style="font-size:11px;color:var(--mist)">2</span><span class="cap" style="font-size:5px">Akademische Stationen</span>
    <span style="font-size:11px;color:var(--mist)">3</span><span class="cap" style="font-size:5px">Konferenzbeiträge</span>
    <span style="font-size:11px;color:var(--mist)">4</span><span class="cap" style="font-size:5px">Veröffentlichungen</span>
    <span style="font-size:11px;color:var(--mist)">5</span><span class="cap" style="font-size:5px">Berufliche Stationen</span>
    <span style="font-size:11px;color:var(--mist)">6</span><span class="cap" style="font-size:5px">Weiterbildungen</span>
    <span style="font-size:11px;color:var(--mist)">7</span><span class="cap" style="font-size:5px">Newsletter</span>
  </div>
</div></section>

<!-- 4 welcome -->
<section class="cell"><div class="slide">
  <div class="pg">4</div>
  <div class="c" style="left:0;right:0;top:8px;font-size:17px;font-weight:700">Begrüßungsrede</div>
  <div style="left:129px;top:58px;width:127px;height:183px;background:var(--pale)"></div>
  <div class="ph" role="img" aria-label="Porträtfoto der Trainerin im Büro" style="left:0;top:41px;width:130px;height:171px"></div>
  <div style="left:140px;top:70px;font-size:6px;font-weight:700">Marlene Vogt</div>
  <div style="left:140px;top:79px;font-size:5px;color:var(--blue)">Name des Trainers</div>
  <div style="left:148px;top:196px;width:55px;height:1px;background:#333"></div>
  <div class="r lead" style="right:20px;top:68px">Eine gute Idee macht<br><b>Alles besser</b></div>
  <div class="bar" style="right:20px;top:106px"></div>
  <div class="copy r" style="right:20px;top:118px;width:160px">Nam quam nunc, blandit vel, luctus pulvinar, hendrerit id, lorem. Maecenas nec odio et ante tincidunt tempus. Donec vitae sapien ut libero venenatis faucibus. Nullam quis ante. Etiam sit amet orci eget eros faucibus tincidunt. Duis leo. Sed fringilla mauris sit amet nibh.</div>
  <div class="foot"><i></i>Dr. Lena Hartwig-Brandt</div>
</div></section>

<!-- 5 text + image -->
<section class="cell"><div class="slide">
  <div class="pg">5</div>
  <div class="h1" style="left:13px;top:12px">Hauptüberschrift hier</div>
  <div class="lead" style="left:13px;top:38px">Eine gute Idee macht<br><b>Alles besser</b></div>
  <div class="bar" style="left:13px;top:80px"></div>
  <div class="copy j" style="left:13px;top:92px;width:118px">Lorem ipsum dolor sit amet, consectetuer adipiscing elit. Aenean commodo ligula eget dolor. Aenean massa. Cum sociis natoque penatibus et magnis dis parturient montes, nascetur ridiculus mus. Donec quam felis, ultricies nec, pellentesque eu, pretium quis, sem. Nulla consequat massa quis enim. Donec pede justo, fringilla vel, aliquet nec, vulputate eget, arcu.</div>
  <div class="ph warm" role="img" aria-label="Foto eines Konferenzpublikums vor einer Bühne" style="left:239px;top:37px;width:214px;height:216px"></div>
</div></section>

<!-- 6 two-column -->
<section class="cell"><div class="slide">
  <div class="pg">6</div>
  <div class="c" style="left:0;right:0;top:10px;font-size:19px;font-weight:700">Dr. Lena Hartwig-Brandt</div>
  <div class="c" style="left:0;right:0;top:35px;font-size:13px">Expertin für Didaktik und Selbstführung</div>
  <div class="bar" style="left:220px;top:57px"></div>
  <div class="copy j" style="left:15px;top:68px;width:200px">Lorem ipsum dolor sit amet, consectetuer adipiscing elit. Aenean commodo ligula eget dolor. Aenean massa. Cum sociis natoque penatibus et magnis dis parturient montes, nascetur ridiculus mus. Donec quam felis, ultricies nec, pellentesque eu, pretium quis, sem. Nulla consequat massa quis enim. Donec pede justo, fringilla vel, aliquet nec, vulputate eget, arcu. In enim justo, rhoncus ut, imperdiet a, venenatis vitae, justo. Nullam dictum felis eu pede mollis pretium. Integer tincidunt.</div>
  <div class="copy j" style="left:238px;top:68px;width:200px">Aenean leo ligula, porttitor eu, consequat vitae, eleifend ac, enim. Aliquam lorem ante, dapibus in, viverra quis, feugiat a, tellus. Phasellus viverra nulla ut metus varius laoreet. Quisque rutrum. Aenean imperdiet. Etiam ultricies nisi vel augue. Curabitur ullamcorper ultricies nisi. Nam eget dui. Etiam rhoncus. Maecenas tempus, tellus eget condimentum rhoncus, sem quam semper libero, sit amet adipiscing sem neque sed ipsum.</div>
  <div class="foot"><i></i>Dr. Lena Hartwig-Brandt</div>
</div></section>

<!-- 7 three features -->
<section class="cell"><div class="slide">
  <div class="pg">7</div>
  <div class="h1" style="left:15px;top:10px">Hauptüberschrift hier</div>
  <div class="copy c" style="left:15px;width:423px;top:36px">Lorem ipsum dolor sit amet, consectetuer adipiscing elit. Aenean commodo ligula eget dolor. Aenean massa. Cum sociis natoque penatibus et magnis dis parturient montes, nascetur ridiculus mus. Donec quam felis, ultricies nec, pellentesque eu, pretium quis, sem. Nulla consequat massa quis enim. Donec pede justo, fringilla vel.</div>
  <div class="dot" style="left:53px;top:93px;width:22px;height:22px"><svg width="10" height="10" viewBox="0 0 10 10"><circle cx="5" cy="3" r="2" fill="#fff"/><path d="M1 10a4 4 0 0 1 8 0z" fill="#fff"/></svg></div>
  <div class="dot" style="left:213px;top:93px;width:22px;height:22px"><svg width="10" height="10" viewBox="0 0 10 10"><path d="M5 9 1 4l2-3h4l2 3z" fill="none" stroke="#fff" stroke-width="1"/></svg></div>
  <div class="dot" style="left:373px;top:93px;width:22px;height:22px"><svg width="11" height="10" viewBox="0 0 11 10"><path d="M.5 4 5.5 1.5 10.5 4 5.5 6.5z" fill="#fff"/><path d="M3 5.5v2.5h5V5.5" fill="none" stroke="#fff"/></svg></div>
  <div class="cap c" style="left:14px;width:100px;top:126px">Hochschuldidaktik</div>
  <div class="cap c" style="left:174px;width:100px;top:121px;line-height:1.8">Aktivierende<br>Methoden</div>
  <div class="cap c" style="left:334px;width:100px;top:126px">Prüfungsdidaktik</div>
  <div class="copy c" style="left:14px;width:100px;top:152px">Nam quam nunc, blandit vel, luctus pulvinar, hendrerit id, lorem. Maecenas nec odio et ante tincidunt tempus.</div>
  <div class="copy c" style="left:174px;width:100px;top:152px">Nam quam nunc, blandit vel, luctus pulvinar, hendrerit id, lorem. Maecenas nec odio et ante tincidunt tempus.</div>
  <div class="copy c" style="left:334px;width:100px;top:152px">Nam quam nunc, blandit vel, luctus pulvinar, hendrerit id, lorem. Maecenas nec odio et ante tincidunt tempus.</div>
  <div class="foot"><i></i>Dr. Lena Hartwig-Brandt</div>
</div></section>

<!-- 8 diamond image -->
<section class="cell"><div class="slide">
  <div class="pg">8</div>
  <div class="h1" style="left:28px;top:10px">Lernen am Arbeitsplatz</div>
  <div style="left:55px;top:88px;width:120px;height:120px;background:var(--pale);transform:rotate(45deg)"></div>
  <div class="ph room" role="img" aria-label="Foto eines Trainers an der Tafel vor Teilnehmenden" style="left:41px;top:76px;width:120px;height:120px;transform:rotate(45deg)"></div>
  <div class="lead" style="left:238px;top:66px">Eine gute Idee macht<br><b>Alles besser</b></div>
  <div class="bar" style="left:416px;top:100px"></div>
  <div class="copy j" style="left:238px;top:112px;width:188px">Lorem ipsum dolor sit amet, consectetuer adipiscing elit. Aenean commodo ligula eget dolor. Aenean massa. Cum sociis natoque penatibus et magnis dis parturient montes, nascetur ridiculus mus. Donec quam felis, ultricies nec, pellentesque eu, pretium quis, sem. Nulla consequat massa quis enim. Donec pede justo, fringilla vel, aliquet nec, vulputate eget, arcu. In enim justo, rhoncus ut, imperdiet a, venenatis vitae, justo. Nullam dictum felis eu pede mollis pretium.</div>
  <div class="foot"><i></i>Dr. Lena Hartwig-Brandt</div>
</div></section>

<!-- 9 blue panel + grid -->
<section class="cell"><div class="slide">
  <div style="left:0;top:0;width:181px;height:253px;background:var(--blue)"></div>
  <div class="lead" style="left:12px;top:50px;color:#fff">Schreiben Sie hier<br><b>Ihre Überschrift.</b></div>
  <div class="bar" style="left:12px;top:88px;background:var(--mist-light)"></div>
  <div style="left:12px;top:105px;color:#fff;font-size:5.6px;font-weight:700">Kunde:</div>
  <div style="left:12px;top:114px;color:#fff;font-size:5px">Nordlicht GmbH</div>
  <div style="left:12px;top:130px;color:#fff;font-size:5.6px;font-weight:700">Beschreibung:</div>
  <div class="copy" style="left:12px;top:140px;width:150px;color:#e4ecf5">Nam quam nunc, blandit vel, luctus pulvinar, hendrerit id, lorem. Maecenas nec odio et ante tincidunt tempus. Donec vitae sapien ut libero venenatis faucibus.</div>
  <div class="ph sky" role="img" aria-label="Foto eines modernen Firmengebäudes" style="left:181px;top:0;width:135px;height:126px"></div>
  <div class="ph warm" role="img" aria-label="Foto eines hellen Foyers" style="left:317px;top:0;width:136px;height:126px"></div>
  <div class="ph warm" role="img" aria-label="Foto eines Konferenzpublikums" style="left:181px;top:127px;width:135px;height:126px"></div>
  <div class="ph" role="img" aria-label="Foto eines Handschlags vor einer Stadtkulisse" style="left:317px;top:127px;width:136px;height:126px"></div>
</div></section>

<!-- 10 full image + boxes -->
<section class="cell"><div class="slide">
  <div class="ph sky" role="img" aria-label="Foto von Hochhäusern im Gegenlicht" style="left:0;top:0;width:453px;height:253px"></div>
  <div style="left:305px;top:0;width:148px;height:146px;background:var(--blue)"></div>
  <div style="right:6px;top:9px;font-size:5px;color:#fff">10</div>
  <div style="left:316px;top:45px;color:#fff;font-size:6px;font-weight:700">Beschreibung:</div>
  <div class="copy" style="left:316px;top:57px;width:125px;color:#e4ecf5">Nam quam nunc, blandit vel, luctus pulvinar, hendrerit id, lorem. Maecenas nec odio et ante tincidunt tempus. Donec vitae sapien ut libero venenatis faucibus.</div>
  <div style="left:253px;top:148px;width:142px;height:105px;background:#fff"></div>
  <div style="left:261px;top:160px;font-size:11px;line-height:1.2;white-space:nowrap">Schreiben Sie hier<br><b style="font-weight:600">Ihre Überschrift.</b></div>
  <div class="bar" style="left:261px;top:192px;width:10px;height:3px"></div>
  <div style="left:261px;top:215px;font-size:6px;font-weight:700">Kunde:</div>
  <div style="left:261px;top:225px;font-size:5.6px">Nordlicht GmbH</div>
  <div class="c" style="left:395px;top:148px;width:58px;height:60px;background:var(--mist);color:#fff;font-size:11px;padding-top:8px;line-height:1.1">18<br><span style="display:block;width:10px;height:1px;background:#fff;margin:3px auto"></span><span style="font-size:5px">Mar/16</span></div>
  <div style="left:395px;top:208px;width:58px;height:45px;background:var(--blue)"></div>
</div></section>

<!-- 11 text + image -->
<section class="cell"><div class="slide">
  <div class="pg">11</div>
  <div class="lead" style="left:13px;top:48px">Schreiben Sie hier<br><b>Ihre Überschrift.</b></div>
  <div class="bar" style="left:13px;top:86px"></div>
  <div style="left:13px;top:102px;font-size:6px;font-weight:700">Beschreibung:</div>
  <div class="copy" style="left:13px;top:112px;width:155px">Nam quam nunc, blandit vel, luctus pulvinar, hendrerit id, lorem. Maecenas nec odio et ante tincidunt tempus. Donec vitae sapien ut libero venenatis faucibus.</div>
  <div class="ph room" role="img" aria-label="Foto eines Teams im Großraumbüro" style="left:181px;top:50px;width:244px;height:174px"></div>
  <div class="foot"><i></i>Dr. Lena Hartwig-Brandt</div>
</div></section>

<!-- 12 image left + date -->
<section class="cell"><div class="slide">
  <div class="pg">12</div>
  <div class="ph warm" role="img" aria-label="Foto eines Workshops mit Haftnotizen an einer Wand" style="left:0;top:0;width:176px;height:253px"></div>
  <div class="c" style="left:139px;top:90px;width:74px;height:74px;background:var(--mist);color:#fff;font-size:14px;padding-top:13px;line-height:1.1">18<br><span style="display:block;width:12px;height:1px;background:#fff;margin:4px auto"></span><span style="font-size:6px">Mar/16</span></div>
  <div class="r lead" style="right:17px;top:46px">Schreiben Sie hier<br><b>Ihre Überschrift.</b></div>
  <div class="bar" style="right:17px;top:84px"></div>
  <div class="r" style="right:17px;top:100px;font-size:6px;font-weight:700">Beschreibung:</div>
  <div class="copy r" style="right:17px;top:112px;width:165px">Lorem ipsum dolor sit amet, consectetuer adipiscing elit. Aenean commodo ligula eget dolor. Aenean massa. Cum sociis natoque penatibus et magnis dis parturient montes, nascetur ridiculus mus. Donec quam felis, ultricies nec, pellentesque eu, pretium quis, sem.</div>
  <div class="foot"><i></i>Dr. Lena Hartwig-Brandt</div>
</div></section>

<!-- 13 four services -->
<section class="cell"><div class="slide">
  <div class="pg">13</div>
  <div class="dot" style="left:22px;top:50px;width:22px;height:22px"><svg width="10" height="10" viewBox="0 0 10 10"><rect x="1" y="1" width="8" height="5" fill="none" stroke="#fff"/><path d="M5 6v3M3 9h4" stroke="#fff"/></svg></div>
  <div class="svc-head" style="left:62px;top:37px">Support für<br>Promovierende</div>
  <div class="copy" style="left:62px;top:73px;width:135px">Nam quam nunc, blandit vel, luctus pulvinar, hendrerit id, lorem. Maecenas nec odio et ante tincidunt tempus. Donec vitae sapien ut libero venenatis faucibus.</div>
  <div class="dot" style="left:235px;top:50px;width:22px;height:22px;background:none;border:1.6px solid var(--blue)"><svg width="10" height="10" viewBox="0 0 10 10"><circle cx="5" cy="5" r="4" fill="none" stroke="#1f5c99"/><path d="M5 2.5V5l2 1" stroke="#1f5c99" fill="none"/></svg></div>
  <div class="svc-head" style="left:274px;top:37px">Selbst- &amp;<br>Zeitmanagement</div>
  <div class="copy" style="left:274px;top:73px;width:135px">Nam quam nunc, blandit vel, luctus pulvinar, hendrerit id, lorem. Maecenas nec odio et ante tincidunt tempus. Donec vitae sapien ut libero venenatis faucibus.</div>
  <div class="dot" style="left:22px;top:150px;width:22px;height:22px"><svg width="10" height="10" viewBox="0 0 10 10"><rect x="1" y="1" width="8" height="6" fill="none" stroke="#fff"/><path d="M3.5 5V3.5M5 5V2.5M6.5 5V4" stroke="#fff"/></svg></div>
  <div class="svc-head" style="left:62px;top:137px">Zielerreichung<br>mit Zielcoaching</div>
  <div class="copy" style="left:62px;top:173px;width:135px">Nam quam nunc, blandit vel, luctus pulvinar, hendrerit id, lorem. Maecenas nec odio et ante tincidunt tempus. Donec vitae sapien ut libero venenatis faucibus.</div>
  <div class="dot" style="left:235px;top:150px;width:22px;height:22px"><svg width="10" height="10" viewBox="0 0 10 10"><rect x="1" y="3" width="8" height="6" rx="1" fill="none" stroke="#fff"/><path d="M3.5 3V1.5h3V3M1 5.5h8" stroke="#fff" fill="none"/></svg></div>
  <div class="svc-head" style="left:274px;top:137px">Stressfrei<br>promovieren</div>
  <div class="copy" style="left:274px;top:173px;width:135px">Nam quam nunc, blandit vel, luctus pulvinar, hendrerit id, lorem. Maecenas nec odio et ante tincidunt tempus. Donec vitae sapien ut libero venenatis faucibus.</div>
  <div class="foot"><i></i>Dr. Lena Hartwig-Brandt</div>
</div></section>

<!-- 14 process timeline -->
<section class="cell"><div class="slide">
  <div class="pg">14</div>
  <div class="h1" style="left:12px;top:10px">Hauptüberschrift hier</div>
  <svg style="left:0;top:0" width="453" height="253" viewBox="0 0 453 253">
    <g fill="none" stroke="#555" stroke-width=".7" stroke-dasharray="2 2"><path d="M35 76v40M146 76v40M257 76v40M368 76v40"/></g>
    <g fill="#1f5c99"><circle cx="35" cy="119" r="2"/><circle cx="146" cy="119" r="2"/><circle cx="257" cy="119" r="2"/><circle cx="368" cy="119" r="2"/></g>
  </svg>
  <div class="c cap" style="left:11px;top:59px;width:48px;height:17px;border:.8px solid #333;font-size:4px;padding-top:3px;line-height:1.3">Hier einen Titel<br>einfügen</div>
  <div class="c cap" style="left:122px;top:59px;width:48px;height:17px;border:.8px solid #333;font-size:4px;padding-top:3px;line-height:1.3">Hier einen Titel<br>einfügen</div>
  <div class="c cap" style="left:233px;top:59px;width:48px;height:17px;border:.8px solid #333;font-size:4px;padding-top:3px;line-height:1.3">Hier einen Titel<br>einfügen</div>
  <div class="c cap" style="left:344px;top:59px;width:48px;height:17px;border:.8px solid #333;font-size:4px;padding-top:3px;line-height:1.3">Hier einen Titel<br>einfügen</div>
  <div class="copy c" style="left:-5px;top:137px;width:80px">Nam quam nunc, blandit vel, luctus pulvinar, hendrerit id, lorem. Maecenas nec odio et ante tincidunt tempus. Donec vitae sapien ut libero venenatis faucibus.</div>
  <div class="copy c" style="left:106px;top:137px;width:80px">Nam quam nunc, blandit vel, luctus pulvinar, hendrerit id, lorem. Maecenas nec odio et ante tincidunt tempus. Donec vitae sapien ut libero venenatis faucibus.</div>
  <div class="copy c" style="left:217px;top:137px;width:80px">Nam quam nunc, blandit vel, luctus pulvinar, hendrerit id, lorem. Maecenas nec odio et ante tincidunt tempus. Donec vitae sapien ut libero venenatis faucibus.</div>
  <div class="copy c" style="left:328px;top:137px;width:80px">Nam quam nunc, blandit vel, luctus pulvinar, hendrerit id, lorem. Maecenas nec odio et ante tincidunt tempus. Donec vitae sapien ut libero venenatis faucibus.</div>
  <div class="foot"><i></i>Dr. Lena Hartwig-Brandt</div>
</div></section>

<!-- 15 quote -->
<section class="cell"><div class="slide">
  <div class="pg">15</div>
  <div class="ph" role="img" aria-label="Kreisförmiges Porträtfoto, abgedunkelt" style="left:159px;top:31px;width:135px;height:135px;border-radius:50%;background:radial-gradient(circle,#6f7782,#3d444d)"></div>
  <div class="c" style="left:159px;top:52px;width:135px;color:#fff;font-size:16px;font-weight:800;line-height:.8">“</div>
  <div class="c" style="left:172px;top:70px;width:109px;color:#fff;font-size:6.4px;font-weight:600;line-height:1.35">Lerne aus der Vergangenheit, lebe im Heute, hoffe auf die Zukunft. Wichtig ist, niemals aufzuhören zu hinterfragen.</div>
  <div class="c" style="left:172px;top:140px;width:109px;color:var(--mist-light);font-size:5px">Unbekannt</div>
  <div class="copy c" style="left:88px;width:277px;top:182px">Lorem ipsum dolor sit amet, consectetuer adipiscing elit. Aenean commodo ligula eget dolor. Aenean massa. Cum sociis natoque penatibus et magnis dis parturient montes, nascetur ridiculus mus. Donec quam felis, ultricies nec, pellentesque eu, pretium quis, sem. Nulla consequat massa quis enim.</div>
  <div class="foot"><i></i>Dr. Lena Hartwig-Brandt</div>
</div></section>

<!-- 16 hub model -->
<section class="cell"><div class="slide">
  <div class="pg">16</div>
  <div class="h1" style="left:23px;top:10px">Hauptüberschrift hier</div>
  <svg style="left:0;top:0" width="453" height="253" viewBox="0 0 453 253">
    <circle cx="228" cy="138" r="40" fill="none" stroke="#1f5c99" stroke-width=".7" stroke-dasharray="1.5 1.5"/>
    <g stroke="#777" stroke-width=".6" stroke-dasharray="1.5 1.5"><path d="M183 88l14 16M273 88l-14 16M164 138h22M292 138h-22M183 188l14-16M273 188l-14-16"/></g>
    <circle cx="228" cy="138" r="32" fill="#1f5c99"/>
    <g fill="none" stroke="#8aa6c2" stroke-width="1"><circle cx="170" cy="81" r="14"/><circle cx="285" cy="81" r="14"/><circle cx="149" cy="138" r="14"/><circle cx="306" cy="138" r="14"/><circle cx="174" cy="196" r="14"/><circle cx="286" cy="196" r="14"/></g>
    <g fill="#e8eef5"><circle cx="170" cy="81" r="12"/><circle cx="285" cy="81" r="12"/><circle cx="149" cy="138" r="12"/><circle cx="306" cy="138" r="12"/><circle cx="174" cy="196" r="12"/><circle cx="286" cy="196" r="12"/></g>
    <g fill="none" stroke="#6f8db0" stroke-width="1"><rect x="165" y="77" width="10" height="8"/><path d="M285 75l2 4 4 .5-3 3 1 4-4-2-4 2 1-4-3-3 4-.5z"/><path d="M146 133h6l1 9h-8z"/><circle cx="306" cy="138" r="4"/><circle cx="174" cy="196" r="2"/><ellipse cx="174" cy="196" rx="6" ry="2.5"/><path d="M282 192c1 4 4 7 8 8"/></g>
  </svg>
  <div class="c" style="left:196px;top:128px;width:64px;color:#fff;font-size:6.5px;font-weight:600;line-height:1.2">TEXTTITEL<br>HIER</div>
  <div class="r" style="right:302px;top:58px;width:85px"><div style="font-size:6.5px;font-weight:600">Texttitel hier</div><div class="copy">Maecenas nec odio et ante tincidunt tempus.</div></div>
  <div style="left:305px;top:58px;width:85px"><div style="font-size:6.5px;font-weight:600">Texttitel hier</div><div class="copy">Maecenas nec odio et ante tincidunt tempus.</div></div>
  <div class="r" style="right:323px;top:118px;width:85px"><div style="font-size:6.5px;font-weight:600">Texttitel hier</div><div class="copy">Maecenas nec odio et ante tincidunt tempus.</div></div>
  <div style="left:326px;top:118px;width:85px"><div style="font-size:6.5px;font-weight:600">Texttitel hier</div><div class="copy">Maecenas nec odio et ante tincidunt tempus.</div></div>
  <div class="r" style="right:298px;top:174px;width:85px"><div style="font-size:6.5px;font-weight:600">Texttitel hier</div><div class="copy">Maecenas nec odio et ante tincidunt tempus.</div></div>
  <div style="left:306px;top:174px;width:85px"><div style="font-size:6.5px;font-weight:600">Texttitel hier</div><div class="copy">Maecenas nec odio et ante tincidunt tempus.</div></div>
  <div class="foot"><i></i>Dr. Lena Hartwig-Brandt</div>
</div></section>

<!-- 17 service flags -->
<section class="cell"><div class="slide">
  <div class="pg">17</div>
  <div class="h1" style="left:13px;top:10px">Hauptüberschrift hier</div>
  <svg style="left:0;top:0" width="453" height="253" viewBox="0 0 453 253">
    <g fill="#1f5c99"><path d="M10 38h87v60H10z"/><path d="M118 38h87v60h-87z"/><path d="M226 38h87v60h-87z"/><path d="M334 38h87v60h-87z"/></g>
    <g fill="#8aa6c2"><path d="M58 112l39-14H76z"/><path d="M166 112l39-14h-21z"/><path d="M274 112l39-14h-21z"/><path d="M382 112l39-14h-21z"/></g>
  </svg>
  <div style="left:19px;top:42px;color:#fff;font-size:14px;line-height:1">Service<br><b style="font-weight:600">Eins</b></div>
  <div style="left:127px;top:42px;color:#fff;font-size:14px;line-height:1">Service<br><b style="font-weight:600">zwei</b></div>
  <div style="left:235px;top:42px;color:#fff;font-size:14px;line-height:1">Service<br><b style="font-weight:600">Drei</b></div>
  <div style="left:343px;top:42px;color:#fff;font-size:14px;line-height:1">Service<br><b style="font-weight:600">Vier</b></div>
  <div class="copy" style="left:10px;top:128px;width:85px">Lorem ipsum dolor sit amet, consectetuer adipiscing elit. Aenean commodo ligula eget dolor. Aenean massa. Cum sociis natoque penatibus et magnis dis parturient montes nascetur.</div>
  <div class="copy" style="left:118px;top:128px;width:85px">Lorem ipsum dolor sit amet, consectetuer adipiscing elit. Aenean commodo ligula eget dolor. Aenean massa. Cum sociis natoque penatibus et magnis dis parturient montes nascetur.</div>
  <div class="copy" style="left:226px;top:128px;width:85px">Lorem ipsum dolor sit amet, consectetuer adipiscing elit. Aenean commodo ligula eget dolor. Aenean massa. Cum sociis natoque penatibus et magnis dis parturient montes nascetur.</div>
  <div class="copy" style="left:334px;top:128px;width:85px">Lorem ipsum dolor sit amet, consectetuer adipiscing elit. Aenean commodo ligula eget dolor. Aenean massa. Cum sociis natoque penatibus et magnis dis parturient montes nascetur.</div>
  <div class="foot"><i></i>Dr. Lena Hartwig-Brandt</div>
</div></section>

<!-- 18 industry description -->
<section class="cell"><div class="slide">
  <div class="pg">18</div>
  <div class="c" style="left:0;right:0;top:6px;font-size:16px;font-weight:700">Industry Description</div>
  <div style="left:0;top:29px;width:453px;height:28px;background:var(--pale)"></div>
  <div style="left:226px;top:29px;width:.7px;height:224px;border-left:.7px dashed #999"></div>
  <div style="left:8px;top:27px;font-size:24px;font-weight:700;color:var(--blue);line-height:1.2">03</div>
  <div style="left:42px;top:29px;font-size:11px;font-weight:600;line-height:1.15;white-space:nowrap">Hier einen Texttitel<br>einfügen</div>
  <div style="left:236px;top:27px;font-size:24px;font-weight:700;color:var(--blue);line-height:1.2">04</div>
  <div style="left:270px;top:29px;font-size:11px;font-weight:600;line-height:1.15;white-space:nowrap">Hier einen<br>Texttitel einfügen</div>
  <div class="c" style="left:10px;top:70px;width:206px"><div class="cap" style="margin-bottom:3px">Texttitel hier</div><div class="copy">Nam quam nunc, blandit vel, luctus pulvinar, hendrerit id, lorem. Maecenas nec odio et ante tincidunt tempus.</div></div>
  <div class="c" style="left:10px;top:98px;width:206px"><div class="cap" style="margin-bottom:3px">Texttitel hier</div><div class="copy">Nam quam nunc, blandit vel, luctus pulvinar, hendrerit id, lorem. Maecenas nec odio et ante tincidunt tempus.</div></div>
  <div class="c" style="left:10px;top:126px;width:206px"><div class="cap" style="margin-bottom:3px">Texttitel hier</div><div class="copy">Nam quam nunc, blandit vel, luctus pulvinar, hendrerit id, lorem. Maecenas nec odio et ante tincidunt tempus.</div></div>
  <div class="dot" style="left:243px;top:72px;width:20px;height:20px"><svg width="9" height="9" viewBox="0 0 9 9"><path d="M.5 4 8.5.5 6 8.5 4 5z" fill="none" stroke="#fff" stroke-width=".8"/></svg></div>
  <div class="dot" style="left:243px;top:101px;width:20px;height:20px"><svg width="9" height="9" viewBox="0 0 9 9"><rect x=".5" y="2.5" width="8" height="6" fill="none" stroke="#fff" stroke-width=".8"/><path d="M3 2.5V1h3v1.5" fill="none" stroke="#fff" stroke-width=".8"/></svg></div>
  <div class="dot" style="left:243px;top:130px;width:20px;height:20px"><svg width="9" height="9" viewBox="0 0 9 9"><rect x=".5" y=".5" width="8" height="8" fill="none" stroke="#fff" stroke-width=".8"/><path d="M3.5 3v3l2.5-1.5z" fill="#fff"/></svg></div>
  <div class="copy" style="left:270px;top:72px;width:170px">Nam quam nunc, blandit vel, luctus pulvinar, hendrerit id, lorem. Maecenas nec odio et ante tincidunt tempus.</div>
  <div class="copy" style="left:270px;top:101px;width:170px">Nam quam nunc, blandit vel, luctus pulvinar, hendrerit id, lorem. Maecenas nec odio et ante tincidunt tempus.</div>
  <div class="copy" style="left:270px;top:130px;width:170px">Nam quam nunc, blandit vel, luctus pulvinar, hendrerit id, lorem. Maecenas nec odio et ante tincidunt tempus.</div>
  <div class="foot"><i></i>Dr. Lena Hartwig-Brandt</div>
</div></section>

<!-- 19 gender split -->
<section class="cell"><div class="slide">
  <div class="pg">19</div>
  <div class="h1" style="left:13px;top:10px">Hauptüberschrift hier</div>
  <svg style="left:0;top:0" width="453" height="253" viewBox="0 0 453 253">
    <circle cx="93" cy="91" r="17" fill="#e8eef5"/>
    <circle cx="363" cy="91" r="17" fill="#e8eef5"/>
    <line x1="230" y1="54" x2="230" y2="150" stroke="#ddd" stroke-width=".6"/>
    <g fill="#1f5c99"><circle cx="178" cy="61" r="6"/><path d="M168 70h20l2 40h-5v44h-5v-34h-4v34h-5v-44h-5z"/></g>
    <g fill="#8aa6c2"><circle cx="282" cy="61" r="6"/><path d="M276 70h12l8 40h-6v44h-4v-34h-4v34h-4v-44h-6z"/></g>
  </svg>
  <div class="c" style="left:68px;top:81px;width:50px;font-size:13px;font-weight:700;color:var(--blue)">65%</div>
  <div class="c" style="left:338px;top:81px;width:50px;font-size:13px;font-weight:600;color:var(--mist)">45%</div>
  <div class="cap c" style="left:73px;top:116px;width:40px;font-size:5px">MAN'S</div>
  <div class="cap c" style="left:338px;top:116px;width:50px;font-size:5px">WOMEN'S</div>
  <div style="left:13px;top:164px;font-size:5.6px;font-weight:700">Details:</div>
  <div class="copy" style="left:13px;top:175px;width:190px">Nam quam nunc, blandit vel, luctus pulvinar, hendrerit id, lorem. Maecenas nec odio et ante tincidunt tempus. Donec vitae sapien ut libero venenatis faucibus.</div>
  <div class="r" style="right:13px;top:164px;font-size:5.6px;font-weight:700">Details:</div>
  <div class="copy r" style="right:13px;top:175px;width:190px">Nam quam nunc, blandit vel, luctus pulvinar, hendrerit id, lorem. Maecenas nec odio et ante tincidunt tempus. Donec vitae sapien ut libero venenatis faucibus.</div>
  <div class="foot"><i></i>Dr. Lena Hartwig-Brandt</div>
</div></section>

<!-- 20 sales expectation -->
<section class="cell"><div class="slide">
  <div class="pg">20</div>
  <div class="h1" style="left:13px;top:6px">Hauptüberschrift hier</div>
  <svg style="left:0;top:0" width="453" height="253" viewBox="0 0 453 253">
    <circle cx="226" cy="84" r="38" fill="#dde5ee"/>
    <circle cx="226" cy="84" r="33" fill="#1f5c99"/>
    <path d="M68 140H380M226 122v18" stroke="#555" stroke-width=".6" stroke-dasharray="1.5 1.5" fill="none"/>
    <g fill="#333"><circle cx="68" cy="140" r="1.6"/><circle cx="226" cy="140" r="1.6"/><circle cx="380" cy="140" r="1.6"/></g>
    <defs><g id="person"><circle cx="0" cy="0" r="3.2"/><path d="M-5 5h10l4 12h-3l-2-6v18h-3v-11h-2v11h-3V11l-2 6h-3z"/></g></defs>
    <g fill="#8aa6c2"><use href="#person" x="55" y="156"/><use href="#person" x="68" y="154"/><use href="#person" x="81" y="156"/></g>
    <g fill="#1f5c99"><use href="#person" x="213" y="156"/><use href="#person" x="226" y="154"/><use href="#person" x="239" y="156"/></g>
    <g fill="#8aa6c2"><use href="#person" x="367" y="156"/><use href="#person" x="380" y="154"/><use href="#person" x="393" y="156"/></g>
  </svg>
  <div class="c" style="left:193px;top:77px;width:66px;color:#fff;font-size:5.6px;font-weight:700;line-height:1.2">SALES<br>EXPECTATION</div>
  <div class="c" style="left:38px;top:195px;width:60px;font-size:14px;font-weight:700">25%</div>
  <div class="c" style="left:38px;top:216px;width:60px;font-size:5.6px;font-weight:600">Normal</div>
  <div class="c" style="left:196px;top:195px;width:60px;font-size:14px;font-weight:700;color:var(--blue)">50%</div>
  <div class="c" style="left:196px;top:216px;width:60px;font-size:5.6px;font-weight:600">Mitte</div>
  <div class="c" style="left:350px;top:195px;width:60px;font-size:14px;font-weight:700">25%</div>
  <div class="c" style="left:345px;top:216px;width:70px;font-size:5.6px;font-weight:600">Hohes Niveau</div>
</div></section>

<!-- 21 map -->
<section class="cell"><div class="slide">
  <div class="pg">21</div>
  <div class="h1" style="left:10px;top:10px">Deutschlandkarte</div>
  <div role="img" aria-label="Landkarte Deutschlands mit Standortpunkten" style="left:172px;top:35px;width:165px;height:200px;background:linear-gradient(180deg,#d4dbe3,#c3ccd6);border-radius:40% 45% 35% 40%"></div>
  <svg style="left:0;top:0" width="453" height="253" viewBox="0 0 453 253">
    <g stroke="#9fb3c7" stroke-width=".6" fill="none"><path d="M110 124h100"/><path d="M368 110H273"/><path d="M155 192h77"/><path d="M370 202H283"/></g>
    <g fill="#fff" stroke="#6f8db0" stroke-width="1"><circle cx="211" cy="124" r="3.5"/><circle cx="273" cy="110" r="3.5"/><circle cx="233" cy="192" r="3.5"/><circle cx="283" cy="202" r="3.5"/></g>
    <g fill="#fff"><circle cx="84" cy="124" r="26" stroke="#dbe3ec" stroke-width="4"/><circle cx="398" cy="110" r="26" stroke="#dbe3ec" stroke-width="4"/><circle cx="128" cy="203" r="26" stroke="#dbe3ec" stroke-width="4"/><circle cx="370" cy="202" r="26" stroke="#dbe3ec" stroke-width="4"/></g>
    <g fill="none" stroke="#6f8db0" stroke-width="4"><circle cx="84" cy="124" r="26" stroke-dasharray="106 200" transform="rotate(-90 84 124)"/><circle cx="398" cy="110" r="26" stroke-dasharray="106 200" transform="rotate(-90 398 110)"/><circle cx="128" cy="203" r="26" stroke-dasharray="106 200" transform="rotate(-90 128 203)"/><circle cx="370" cy="202" r="26" stroke-dasharray="106 200" transform="rotate(-90 370 202)"/></g>
  </svg>
  <div class="c" style="left:59px;top:111px;width:50px;font-size:7px;line-height:1.15"><b>65%</b><br>Lorem<br>Ipsum</div>
  <div class="c" style="left:373px;top:97px;width:50px;font-size:7px;line-height:1.15"><b>65%</b><br>Lorem<br>Ipsum</div>
  <div class="c" style="left:103px;top:190px;width:50px;font-size:7px;line-height:1.15"><b>65%</b><br>Lorem<br>Ipsum</div>
  <div class="c" style="left:345px;top:189px;width:50px;font-size:7px;line-height:1.15"><b>65%</b><br>Lorem<br>Ipsum</div>
  <div class="foot"><i></i>Dr. Lena Hartwig-Brandt</div>
</div></section>

<!-- 22 donut -->
<section class="cell"><div class="slide">
  <div class="pg">22</div>
  <div class="c" style="left:0;right:0;top:8px;font-size:16px;font-weight:700">Hauptüberschrift hier</div>
  <svg style="left:0;top:0" width="453" height="253" viewBox="0 0 453 253">
    <g transform="rotate(-90 227 145)" fill="none" stroke-width="46">
      <circle cx="227" cy="145" r="68" stroke="#222" stroke-dasharray="85.5 342"/>
      <circle cx="227" cy="145" r="68" stroke="#1f5c99" stroke-dasharray="0 85.5 192 150"/>
      <circle cx="227" cy="145" r="68" stroke="#8aa6c2" stroke-dasharray="0 277.5 98 52"/>
      <circle cx="227" cy="145" r="68" stroke="#5f6b78" stroke-dasharray="0 375.5 52 0"/>
    </g>
    <g fill="#1d1d1d"><rect x="29" y="33" width="7" height="7" fill="#5f6b78"/><rect x="29" y="91" width="7" height="7" fill="#5f6b78"/><rect x="341" y="33" width="7" height="7"/><rect x="341" y="91" width="7" height="7" fill="#1f5c99"/></g>
    <g fill="#fff" font-family="Open Sans,sans-serif" font-size="5" text-anchor="middle"><text x="32.5" y="38.5">1</text><text x="32.5" y="96.5">2</text><text x="344.5" y="38.5">3</text><text x="344.5" y="96.5">4</text></g>
  </svg>
  <div style="left:191px;top:64px;font-size:8px;font-weight:600;color:#fff">20%</div>
  <div style="left:237px;top:64px;font-size:8px;font-weight:600;color:#fff">20%</div>
  <div style="left:146px;top:138px;font-size:7px;color:#fff">35%</div>
  <div style="left:265px;top:171px;font-size:8px;font-weight:600;color:#fff">60%</div>
  <div class="c" style="left:182px;top:127px;width:90px;font-size:12px;line-height:1.05">Shares of<br><b style="font-weight:600">Market</b></div>
  <div style="left:40px;top:32px;font-size:6px;font-weight:700">Texttitel hier</div>
  <div class="copy" style="left:29px;top:44px;width:75px">Lorem ipsum dolor sit amet, consectetuer adipiscing elit. Aenean commodo ligula eget dolor. Aenean massa.</div>
  <div style="left:40px;top:90px;font-size:6px;font-weight:700">Texttitel hier</div>
  <div class="copy" style="left:29px;top:102px;width:75px">Lorem ipsum dolor sit amet, consectetuer adipiscing elit. Aenean commodo ligula eget dolor. Aenean massa.</div>
  <div style="left:352px;top:32px;font-size:6px;font-weight:700">Texttitel hier</div>
  <div class="copy" style="left:341px;top:44px;width:75px">Lorem ipsum dolor sit amet, consectetuer adipiscing elit. Aenean commodo ligula eget dolor. Aenean massa.</div>
  <div style="left:352px;top:90px;font-size:6px;font-weight:700">Texttitel hier</div>
  <div class="copy" style="left:341px;top:102px;width:75px">Lorem ipsum dolor sit amet, consectetuer adipiscing elit. Aenean commodo ligula eget dolor. Aenean massa.</div>
  <div class="foot"><i></i>Dr. Lena Hartwig-Brandt</div>
</div></section>

<!-- 23 data table -->
<section class="cell"><div class="slide">
  <div class="pg">23</div>
  <div class="h1" style="left:15px;top:8px">Hauptüberschrift hier</div>
  <table style="left:9px;top:45px;width:434px;border-collapse:collapse;font-size:5px;text-align:center">
    <thead><tr style="background:var(--blue);color:#fff;font-weight:700;height:17px"><th></th><th>2021</th><th>2022</th><th>2023</th><th>2024</th><th>2025</th></tr></thead>
    <tbody>
      <tr style="height:14px;background:var(--pale)"><td>Ein Text</td><td>234</td><td>234</td><td>234</td><td>234</td><td><b>8.5%</b></td></tr>
      <tr style="height:14px"><td>Text zwei</td><td>97</td><td>97</td><td>97</td><td>97</td><td><b>7%</b></td></tr>
      <tr style="height:14px;background:var(--pale)"><td>Text drei</td><td>55</td><td>55</td><td>55</td><td>55</td><td><b>4.9%</b></td></tr>
      <tr style="height:14px"><td>Text vier</td><td>20</td><td>20</td><td>20</td><td>20</td><td><b>3.2%</b></td></tr>
      <tr style="height:14px;background:var(--pale)"><td>Text fünf</td><td>20</td><td>18</td><td>23</td><td>23</td><td><b>4.2%</b></td></tr>
      <tr style="height:14px;font-weight:700"><td>Gesamt</td><td>426</td><td>420</td><td>429</td><td>429</td><td>20%</td></tr>
    </tbody>
  </table>
  <div class="foot"><i></i>Dr. Lena Hartwig-Brandt</div>
</div></section>

<!-- 24 feature table -->
<section class="cell"><div class="slide">
  <div class="pg">24</div>
  <div class="h1" style="left:13px;top:9px">Hauptüberschrift hier</div>
  <table style="left:8px;top:44px;width:422px;border-collapse:collapse;font-size:4.2px;text-align:center">
    <thead><tr style="background:var(--blue);color:#fff;font-weight:700;height:14px;font-size:4.6px"><th>Eine Spalte</th><th>Spalte zwei</th><th>Spalte drei</th><th>Weakness</th><th>Spalte vier</th><th>Spalte fünf</th><th>Spalte sechs</th></tr></thead>
    <tbody style="font-weight:600">
      <tr style="height:7px;background:var(--pale)"><td>Eine Reihe</td><td>+</td><td></td><td>Beschreibung</td><td></td><td>Beschreibung</td><td></td></tr>
      <tr style="height:7px"><td>Reihe zwei</td><td></td><td>+</td><td></td><td>+</td><td></td><td></td></tr>
      <tr style="height:7px;background:var(--pale)"><td>Reihe drei</td><td></td><td></td><td>+</td><td>Beschreibung</td><td>+</td><td>+</td></tr>
      <tr style="height:7px"><td>Reihe vier</td><td>+</td><td>+</td><td></td><td></td><td></td><td></td></tr>
      <tr style="height:7px;background:var(--pale)"><td>Reihe fünf</td><td></td><td></td><td>-</td><td>Beschreibung</td><td></td><td>-</td></tr>
      <tr style="height:7px"><td>Reihe sechs</td><td>+</td><td>+</td><td></td><td></td><td>+</td><td></td></tr>
      <tr style="height:7px;background:var(--pale)"><td>Reihe sieben</td><td></td><td></td><td></td><td>+</td><td></td><td>+</td></tr>
      <tr style="height:7px"><td>Reihe acht</td><td>Beschreibung</td><td>+</td><td>+</td><td></td><td></td><td></td></tr>
      <tr style="height:7px;background:var(--pale)"><td>Klasse neun</td><td>-</td><td>Beschreibung</td><td>-</td><td>Beschreibung</td><td>-</td><td>Beschreibung</td></tr>
      <tr style="height:7px"><td>Klasse zehn</td><td>+</td><td></td><td></td><td></td><td></td><td></td></tr>
      <tr style="height:7px;background:var(--pale)"><td>elfte Klasse</td><td></td><td>+</td><td>+</td><td>+</td><td>-</td><td>+</td></tr>
      <tr style="height:7px"><td>Zwölf Reihen</td><td>+</td><td></td><td></td><td></td><td></td><td></td></tr>
    </tbody>
  </table>
  <div class="foot"><i></i>Dr. Lena Hartwig-Brandt</div>
</div></section>

<!-- 25 icon list -->
<section class="cell"><div class="slide">
  <div class="pg">25</div>
  <div class="h1" style="left:14px;top:8px">Hauptüberschrift hier</div>
  <div style="left:226px;top:45px;height:160px;border-left:.7px dashed #999"></div>
  <div class="dot" style="left:10px;top:52px;width:22px;height:22px"><svg width="11" height="9" viewBox="0 0 11 9"><circle cx="3.5" cy="2.5" r="2" fill="none" stroke="#fff" stroke-width=".8"/><circle cx="7.5" cy="2.5" r="2" fill="none" stroke="#fff" stroke-width=".8"/><path d="M.5 8.5a3 3 0 0 1 6 0M4.5 8.5a3 3 0 0 1 6 0" fill="none" stroke="#fff" stroke-width=".8"/></svg></div>
  <div class="dot" style="left:10px;top:108px;width:22px;height:22px"><svg width="9" height="9" viewBox="0 0 9 9"><rect x=".5" y="1.5" width="7" height="7" fill="none" stroke="#fff" stroke-width=".8"/><path d="M3 6l5-5" stroke="#fff" stroke-width=".8"/></svg></div>
  <div class="dot" style="left:10px;top:164px;width:22px;height:22px"><svg width="11" height="8" viewBox="0 0 11 8"><circle cx="2.7" cy="5" r="2.2" fill="none" stroke="#fff" stroke-width=".8"/><circle cx="8.3" cy="5" r="2.2" fill="none" stroke="#fff" stroke-width=".8"/><path d="M2 3l1-2.5h5L9 3" fill="none" stroke="#fff" stroke-width=".8"/></svg></div>
  <div class="dot" style="left:420px;top:52px;width:22px;height:22px"><svg width="8" height="10" viewBox="0 0 8 10"><rect x=".5" y="1" width="7" height="8.5" fill="none" stroke="#fff" stroke-width=".8"/><path d="M2 4h4M2 6h4" stroke="#fff" stroke-width=".7"/></svg></div>
  <div class="dot" style="left:420px;top:108px;width:22px;height:22px"><svg width="9" height="9" viewBox="0 0 9 9"><rect x=".5" y=".5" width="8" height="8" rx="1" fill="none" stroke="#fff" stroke-width=".8"/><circle cx="4.5" cy="4.5" r="2" fill="none" stroke="#fff" stroke-width=".7"/></svg></div>
  <div class="dot" style="left:420px;top:164px;width:22px;height:22px"><svg width="9" height="9" viewBox="0 0 9 9"><path d="M1.5.5l2 2-1 1.5c1 1.5 2 2.5 3.5 3.5l1.5-1 2 2-1.5 1.5C4 9 0 5 0 2z" fill="none" stroke="#fff" stroke-width=".8"/></svg></div>
  <div style="left:38px;top:48px;width:170px"><div style="font-size:5.8px;font-weight:700;margin-bottom:2px">Hier Text einfügen</div><div class="copy">Nam quam nunc, blandit vel, luctus pulvinar, hendrerit id, lorem. Maecenas nec odio et ante tincidunt tempus.</div></div>
  <div style="left:38px;top:104px;width:170px"><div style="font-size:5.8px;font-weight:700;margin-bottom:2px">Hier Text einfügen</div><div class="copy">Nam quam nunc, blandit vel, luctus pulvinar, hendrerit id, lorem. Maecenas nec odio et ante tincidunt tempus.</div></div>
  <div style="left:38px;top:160px;width:170px"><div style="font-size:5.8px;font-weight:700;margin-bottom:2px">Hier Text einfügen</div><div class="copy">Nam quam nunc, blandit vel, luctus pulvinar, hendrerit id, lorem. Maecenas nec odio et ante tincidunt tempus.</div></div>
  <div class="r" style="right:38px;top:48px;width:170px"><div style="font-size:5.8px;font-weight:700;margin-bottom:2px">Hier Text einfügen</div><div class="copy">Nam quam nunc, blandit vel, luctus pulvinar, hendrerit id, lorem. Maecenas nec odio et ante tincidunt tempus.</div></div>
  <div class="r" style="right:38px;top:104px;width:170px"><div style="font-size:5.8px;font-weight:700;margin-bottom:2px">Hier Text einfügen</div><div class="copy">Nam quam nunc, blandit vel, luctus pulvinar, hendrerit id, lorem. Maecenas nec odio et ante tincidunt tempus.</div></div>
  <div class="r" style="right:38px;top:160px;width:170px"><div style="font-size:5.8px;font-weight:700;margin-bottom:2px">Hier Text einfügen</div><div class="copy">Nam quam nunc, blandit vel, luctus pulvinar, hendrerit id, lorem. Maecenas nec odio et ante tincidunt tempus.</div></div>
  <div class="foot"><i></i>Dr. Lena Hartwig-Brandt</div>
</div></section>

<!-- 26 chevron process -->
<section class="cell"><div class="slide">
  <div class="pg">26</div>
  <div class="h1" style="left:14px;top:12px">Hauptüberschrift hier</div>
  <svg style="left:0;top:0" width="453" height="253" viewBox="0 0 453 253">
    <path d="M14 117h90l12 19-12 19H14l12-19z" fill="#1f5c99"/>
    <path d="M113 117h90l12 19-12 19h-90l12-19z" fill="#8aa6c2"/>
    <path d="M212 117h90l12 19-12 19h-90l12-19z" fill="#1f5c99"/>
    <path d="M311 117h90l12 19-12 19h-90l12-19z" fill="#8aa6c2"/>
  </svg>
  <div class="cap c" style="left:20px;top:129px;width:90px;color:#fff;font-size:5.5px;line-height:1.2">Hier Text<br>einfügen</div>
  <div class="cap c" style="left:119px;top:129px;width:90px;color:#fff;font-size:5.5px;line-height:1.2">Hier Text<br>einfügen</div>
  <div class="cap c" style="left:218px;top:129px;width:90px;color:#fff;font-size:5.5px;line-height:1.2">Hier Text<br>einfügen</div>
  <div class="cap c" style="left:317px;top:129px;width:90px;color:#fff;font-size:5.5px;line-height:1.2">Hier Text<br>einfügen</div>
  <div class="copy c" style="left:120px;top:60px;width:92px">Nam quam nunc, blandit vel, luctus pulvinar, hendrerit id, lorem. Maecenas nec odio et ante tincidunt tempus.</div>
  <div class="copy c" style="left:318px;top:60px;width:92px">Nam quam nunc, blandit vel, luctus pulvinar, hendrerit id, lorem. Maecenas nec odio et ante tincidunt tempus.</div>
  <div class="copy c" style="left:22px;top:172px;width:92px">Nam quam nunc, blandit vel, luctus pulvinar, hendrerit id, lorem. Maecenas nec odio et ante tincidunt tempus.</div>
  <div class="copy c" style="left:220px;top:172px;width:92px">Nam quam nunc, blandit vel, luctus pulvinar, hendrerit id, lorem. Maecenas nec odio et ante tincidunt tempus.</div>
  <div class="foot"><i></i>Dr. Lena Hartwig-Brandt</div>
</div></section>

<!-- 27 closing -->
<section class="cell"><div class="slide">
  <div style="left:0;top:0;width:50px;height:253px;background:var(--blue)"></div>
  <div class="ph sky" role="img" aria-label="Foto eines gläsernen Bürohochhauses" style="left:227px;top:0;width:226px;height:253px"></div>
  <div style="left:70px;top:30px;display:flex;align-items:center;gap:3px;font-family:'Roboto Condensed',sans-serif;font-weight:700;font-size:8px;color:var(--blue)"><i style="display:block;width:8px;height:8px;border:1px solid var(--blue)"></i>Dr. Lena Hartwig-Brandt</div>
  <div style="left:70px;top:58px;font-size:20px;font-weight:800;line-height:1.2;color:#333">Kontaktier<br>en Sie uns</div>
  <div class="dot" style="left:10px;top:117px;width:27px;height:27px;background:var(--mist-light)"><svg width="11" height="11" viewBox="0 0 9 9"><path d="M1.5.5l2 2-1 1.5c1 1.5 2 2.5 3.5 3.5l1.5-1 2 2-1.5 1.5C4 9 0 5 0 2z" fill="#fff"/></svg></div>
  <div class="dot" style="left:10px;top:156px;width:27px;height:27px;background:var(--mist-light)"><svg width="11" height="8" viewBox="0 0 11 8"><rect width="11" height="8" fill="#fff"/><path d="M0 0l5.5 4.5L11 0" fill="none" stroke="#b9cadb" stroke-width=".8"/></svg></div>
  <div class="dot" style="left:10px;top:195px;width:27px;height:27px;background:var(--mist-light)"><svg width="9" height="12" viewBox="0 0 9 12"><path d="M4.5 12S0 7 0 4.5a4.5 4.5 0 0 1 9 0C9 7 4.5 12 4.5 12z" fill="#fff"/><circle cx="4.5" cy="4.5" r="1.7" fill="#b9cadb"/></svg></div>
  <div style="left:70px;top:125px;font-size:7px;font-weight:600">+01520 / 480 16 93</div>
  <div style="left:70px;top:164px;font-size:7px;font-weight:600">info@lenahartwig.de</div>
  <div style="left:70px;top:198px;font-size:7px;font-weight:600;line-height:1.3">Lindenweg 12<br>96047 BAMBERG</div>
</div></section>

</main>
</body>
</html>
```